Larkfield Ridge Management

I need a professional website. My current website is larkfieldridgemanagement.com and I hate it. It was created with some AI tool very quickly because I needed a site up and running with no advanced notice. I’m open to all designs .. I trust you, the professionals will deliver the results I’m anxiously awaiting! :)

```html
<!DOCTYPE html>
<html lang="en">
<head>
<meta charset="utf-8">
<title>Larkfield Ridge Management</title>
<link rel="stylesheet" href="https://fonts.googleapis.com/css2?family=Marcellus&family=Lato:wght@400;700&display=swap">
<style>
:root{
  --navy:#22325a;
  --red:#d0272d;
  --ink:#333333;
  --text:#4a4a4a;
  --white:#ffffff;
  --footer:#333333;
}
*{box-sizing:border-box;margin:0;padding:0}
html,body{width:1200px;height:4182px;overflow:hidden}
body{position:relative;background:var(--white);font-family:'Lato',sans-serif;color:var(--text)}
.abs{position:absolute}
.serif{font-family:'Marcellus',serif}
.accent{color:var(--red)}
.btn{position:absolute;display:flex;align-items:center;justify-content:center;font-size:15px;letter-spacing:.3px;text-transform:uppercase}
.btn-outline-dark{border:1px solid #333;color:#333;background:#fff}
.btn-solid-light{background:#fff;color:#333}
.btn-outline-light{border:1px solid #fff;color:#fff}

.nav-bar{left:114px;top:52px;width:976px;height:49px;background:var(--navy)}
.nav-link{position:absolute;top:52px;height:49px;display:flex;align-items:center;justify-content:center;color:#fff;font-size:15px;text-transform:uppercase}
.nav-link.active{background:var(--red)}
.brand{left:520px;top:26px;width:160px;height:100px;background:var(--navy);display:flex;align-items:center;justify-content:center;text-align:center;color:#fff;font-weight:700;font-size:16px;line-height:1.25;letter-spacing:.5px}

.hero-photo{left:0;top:154px;width:1200px;height:611px;background:linear-gradient(110deg,#6f6a64 0%,#9c968e 35%,#b9c3cc 65%,#8a9099 100%)}
.hero-panel{left:62px;top:253px;width:469px;height:343px;background:var(--red)}
.hero-title{left:114px;top:302px;color:#fff;font-size:36px;line-height:46px;text-transform:uppercase;font-weight:400}
.hero-sub{left:114px;top:408px;width:380px;color:#fff;font-size:16px;line-height:24px}

.about-title{left:114px;top:872px;font-size:38px;line-height:46px;color:var(--ink);font-weight:400}
.about-text{left:114px;top:994px;width:380px;font-size:15px;line-height:29px}
.photo{position:absolute}

.sec-title{left:0;width:1200px;text-align:center;font-size:38px;color:var(--ink);font-weight:400}
.sec-text{left:160px;width:880px;text-align:center;font-size:15px;line-height:29px}
.card{position:absolute;width:296px;height:266px;display:flex;flex-direction:column;align-items:center;text-align:center;padding-top:36px}
.card.red{background:var(--red);color:#fff}
.card.navy{background:var(--navy);color:#fff}
.card.plain{background:#fff;border:1px solid #cfcfcf;color:var(--text)}
.card h3{font-weight:400;font-size:15px;margin-top:18px;text-transform:uppercase}
.card .rule{width:36px;height:2px;background:currentColor;margin:18px 0 20px}
.card p{font-size:15px;line-height:23px;width:250px}

.inquiry{left:0;top:2360px;width:1200px;height:750px;background:var(--navy)}
.field{position:absolute;border:1px solid #fff;color:#fff;font-size:15px;padding:14px 25px}

.footer{left:0;top:3761px;width:1200px;height:380px;background:var(--footer)}
.foot-bar{left:0;top:4141px;width:1200px;height:41px;background:var(--navy);color:#fff;font-size:13px;display:flex;align-items:center;justify-content:center}
.foot-head{position:absolute;top:3847px;color:#fff;font-weight:700;font-size:17px;text-transform:uppercase}
.foot-list{position:absolute;top:3892px;list-style:none;color:#fff;font-size:15px}
.foot-list li{height:32.5px}
.contact-item{position:absolute;left:555px;color:#fff;font-size:15px;display:flex;align-items:center;gap:12px}
.foot-brand{left:112px;top:3900px;width:210px;color:#fff;font-weight:700;font-size:26px;line-height:32px;text-align:center}
</style>
</head>
<body>

<div class="abs nav-bar"></div>
<div class="nav-link active" style="left:331px;width:73px">Home</div>
<div class="nav-link" style="left:420px;width:88px">Services</div>
<div class="abs brand">LARKFIELD<br>RIDGE</div>
<div class="nav-link" style="left:682px;width:72px">About</div>
<div class="nav-link" style="left:770px;width:90px">Contact</div>

<div class="abs hero-photo" role="img" aria-label="Agent showing a couple around a bright high-rise apartment with city views"></div>
<div class="abs hero-panel"></div>
<h1 class="abs hero-title serif">A true partner, not<br>just a vendor. &#9733;</h1>
<p class="abs hero-sub">Committed to protecting your investment with proactive, dependable service.</p>
<div class="btn btn-solid-light" style="left:114px;top:486px;width:159px;height:48px">Get Started</div>
<div class="btn btn-outline-light" style="left:300px;top:486px;width:153px;height:48px">Learn More</div>

<h2 class="abs about-title serif">About Our Property<br>Management <span class="accent">Solutions</span></h2>
<p class="abs about-text">Our organization delivers comprehensive property management solutions that optimize asset performance and tenant satisfaction. By integrating advanced analytics with proven operational frameworks, our specialists ensure each property achieves sustained value appreciation.</p>
<div class="btn btn-outline-dark" style="left:114px;top:1200px;width:157px;height:51px">Get Started</div>
<div class="photo" style="left:622px;top:870px;width:468px;height:324px;background:linear-gradient(120deg,#8b8f94,#c9ccd0 50%,#a9adb2)" role="img" aria-label="Team of property managers meeting in a bright office"></div>
<div class="photo" style="left:533px;top:1090px;width:305px;height:208px;background:linear-gradient(160deg,#b8c6d6,#7d7f80 55%,#5b6f45)" role="img" aria-label="Modern townhouse exterior"></div>

<h2 class="abs sec-title serif" style="top:1405px">Our Core <span class="accent">Services</span></h2>
<p class="abs sec-text" style="top:1475px">Our analysis demonstrates that effective property oversight originates from meticulous operational planning, transparent communication channels, and data-driven performance metrics across every asset class. By integrating advanced technology with industry expertise, our team implements proactive maintenance schedules that preserve asset value and facilitate sustainable, long-term returns for stakeholders.</p>

<div class="card red" style="left:114px;top:1648px">
  <svg width="36" height="40" viewBox="0 0 36 40" fill="none" stroke="#fff" stroke-width="1.5"><rect x="8" y="2" width="24" height="30"/><rect x="3" y="7" width="24" height="30" fill="#d0272d"/><path d="M8 15h14M8 20h14M8 25h14M8 30h10"/></svg>
  <h3>Basic Service</h3><div class="rule"></div>
  <p>Describe important details like price, value, length of service, and why it's unique.</p>
</div>
<div class="card plain" style="left:453px;top:1648px">
  <svg width="44" height="44" viewBox="0 0 44 44" fill="none" stroke="#333" stroke-width="1.3"><circle cx="22" cy="22" r="20"/><circle cx="22" cy="22" r="14"/><path d="M22 14l2.4 5 5.4.6-4 3.7 1.1 5.3-4.9-2.7-4.9 2.7 1.1-5.3-4-3.7 5.4-.6z"/></svg>
  <h3>Intermediate Service</h3><div class="rule" style="background:#333"></div>
  <p>Describe important details like price, value, length of service, and why it's unique. Or use these sections to</p>
</div>
<div class="card navy" style="left:794px;top:1648px">
  <svg width="44" height="48" viewBox="0 0 44 48" fill="none" stroke="#fff" stroke-width="1.4"><path d="M22 3l18 6v14c0 11-8 19-18 22C12 42 4 34 4 23V9z"/><circle cx="22" cy="22" r="6"/><path d="M19 30h6M20 33h4"/></svg>
  <h3>Advanced Service</h3><div class="rule"></div>
  <p>Describe important details like price, value, length of service, and why it's unique. Or use these sections to</p>
</div>
<div class="photo" style="left:114px;top:1949px;width:296px;height:266px;background:linear-gradient(135deg,#6b5544,#c8b9a4 50%,#e4dccf)" role="img" aria-label="Hands arranging fabric and material samples on a table"></div>
<div class="card navy" style="left:451px;top:1951px">
  <svg width="44" height="44" viewBox="0 0 44 44" fill="none" stroke="#fff" stroke-width="1.4"><circle cx="22" cy="22" r="19" stroke-dasharray="4 3"/><circle cx="22" cy="22" r="13"/><path d="M15 23l7-6 7 6M17 21v7h10v-7"/></svg>
  <h3>Advanced+ Service</h3><div class="rule"></div>
  <p>Describe important details like price, value, length of service, and why it's unique. Or use these sections to</p>
</div>
<div class="photo" style="left:794px;top:1947px;width:296px;height:266px;background:linear-gradient(135deg,#b7a692,#dccbb6 55%,#2a2623)" role="img" aria-label="Decor lamp and stacked swatches on a dark shelf"></div>

<div class="abs inquiry"></div>
<h2 class="abs sec-title serif" style="top:2468px;font-size:40px;color:#fff">Submit Your Property Management Inquiry</h2>
<p class="abs" style="left:170px;top:2540px;width:860px;text-align:center;color:#fff;font-size:15px;line-height:29px">Please complete the inquiry form to facilitate an initial consultation, enabling our team to demonstrate how comprehensive property management solutions can enhance operational efficiency and stakeholder satisfaction.</p>
<div class="field" style="left:122px;top:2639px;width:299px;height:50px">First Name</div>
<div class="field" style="left:450px;top:2639px;width:299px;height:50px">Last Name</div>
<div class="field" style="left:778px;top:2639px;width:299px;height:50px">Email Address</div>
<div class="field" style="left:122px;top:2723px;width:955px;height:160px;padding-top:18px">Message</div>
<div class="btn btn-solid-light" style="left:521px;top:2939px;width:159px;height:49px">Get Started</div>

<div class="photo" style="left:171px;top:3235px;width:453px;height:286px;background:linear-gradient(160deg,#c9cdd6,#8c8f95 50%,#4b5a43)" role="img" aria-label="Contemporary two-storey house at dusk"></div>
<div class="photo" style="left:112px;top:3438px;width:296px;height:226px;background:linear-gradient(120deg,#dfe3e8,#a7b4c4 50%,#3d3f46)" role="img" aria-label="Smiling clients signing papers with an advisor"></div>
<h2 class="abs serif" style="left:698px;top:3240px;font-size:38px;line-height:46px;color:var(--ink);font-weight:400">Ready to Protect Your<br><span class="accent">Investment?</span></h2>
<p class="abs" style="left:698px;top:3359px;width:375px;font-size:15px;line-height:29px">Partner with Larkfield Ridge Management for reliable, transparent property management tailored to your needs.Partner with Larkfield Ridge Management for reliable, transparent property management tailored to your needs.</p>
<div class="btn btn-outline-dark" style="left:698px;top:3539px;width:160px;height:50px">Get Started</div>

<div class="abs footer"></div>
<div class="abs foot-brand">LARKFIELD<br>RIDGE<br>MANAGEMENT</div>

<div class="foot-head" style="left:372px">Quick Links</div>
<ul class="foot-list" style="left:372px"><li>Home</li><li>About Us</li><li>Services</li><li>Contact</li></ul>

<div class="foot-head" style="left:555px">Contact Us</div>
<div class="contact-item" style="top:3894px">
  <svg width="16" height="22" viewBox="0 0 16 22"><path d="M8 0a8 8 0 0 0-8 8c0 6 8 14 8 14s8-8 8-14a8 8 0 0 0-8-8z" fill="#fff"/><circle cx="8" cy="8" r="3" fill="#333"/></svg>
  <span>Larkfield &amp; Ridgemoor Valley</span>
</div>
<div class="contact-item" style="top:3934px">
  <svg width="18" height="18" viewBox="0 0 24 24"><path fill="#fff" d="M6.6 10.8a15 15 0 0 0 6.6 6.6l2.2-2.2a1 1 0 0 1 1-.25 11.4 11.4 0 0 0 3.6.6 1 1 0 0 1 1 1V20a1 1 0 0 1-1 1A17 17 0 0 1 3 4a1 1 0 0 1 1-1h3.5a1 1 0 0 1 1 1c0 1.25.2 2.45.6 3.6a1 1 0 0 1-.25 1z"/></svg>
  <span>(XXX) XXX-XXXX</span>
</div>
<div class="contact-item" style="top:3974px">
  <svg width="20" height="15" viewBox="0 0 20 15"><rect width="20" height="15" rx="1" fill="#fff"/><path d="M1 1l9 7 9-7" fill="none" stroke="#333" stroke-width="1.5"/></svg>
  <span>info@larkfieldridgemanagement.com</span>
</div>

<div class="foot-head" style="left:908px">Services</div>
<ul class="foot-list" style="left:908px"><li>Property Management</li><li>Maintenance Coordination</li><li>Tenant Relations</li><li>Leasing Support</li><li>Financial Reporting</li><li>Asset Preservation</li></ul>

<div class="abs foot-bar">&copy; 2026 LARKFIELD RIDGE MANAGEMENT. ALL RIGHTS RESERVED.</div>

</body>
</html>
```